Satchel & Sundial needs new business card design

I need a new business card design. I'm looking for out-of-the-box design which represents the freedom of being a location independent entrepreneur.
I offer coaching, retreats and trips.
I would like to see designs with and without the photo.
Colors I use are black (#000000), green (#25A796) and brown (#D7C38C)
Website satchelandsundial.example

Target Market(s)

location independent entrepreneurs, digital nomads, people looking to swap the 9 to 5 for a lifestyle business

Industry/Entity Type

Business

Contact Information for Business Card

Dorota Falkner
Your Lifestyle Business Coach, Retreat & Trip Leader
http://satchelandsundial.example
hello@satchelandsundial.example
Live a life you don't need a holiday from

Font styles to use
Serif
Sans Serif

Requirements
Must have
• One side should contain only the logo. I would also consider having the "Live a life you don't need a holiday from" on that side too (depending on how it looks)
• Please show both sides on the designs.

```html
<!DOCTYPE html>
<html lang="en">
<head>
<meta charset="utf-8">
<title>Satchel &amp; Sundial — Business Card</title>
<link rel="stylesheet" href="https://fonts.googleapis.com/css2?family=Arimo:wght@400;700&display=swap">
<style>
  :root {
    --backdrop: #3a3b3d;
    --card-white: #ffffff;
    --card-black: #1c1b1c;
    --ink: #2a2a2a;
    --ink-soft: #555555;
    --teal: #25a796;
    --band-dark: #2b2a2b;
    --band-mid: #5a5a5c;
    --paper-light: #f2f2f2;
  }
  * { box-sizing: border-box; margin: 0; padding: 0; }
  html, body {
    width: 1200px;
    height: 843px;
    overflow: hidden;
    background: var(--backdrop);
    font-family: "Arimo", Arial, sans-serif;
  }
  .canvas {
    position: relative;
    width: 1200px;
    height: 843px;
    display: flex;
    flex-direction: column;
    align-items: center;
    justify-content: center;
    gap: 48px;
  }
  .card {
    position: relative;
    width: 640px;
    height: 366px;
    overflow: hidden;
    box-shadow: 0 10px 28px rgba(0,0,0,0.35);
  }

  /* Back side */
  .card--back { background: var(--card-black); }
  .card--back .wordmark {
    position: absolute;
    left: 0; right: 0;
    top: 136px;
    text-align: center;
    color: var(--card-white);
    font-size: 40px;
    font-weight: 700;
    letter-spacing: 1px;
    text-transform: uppercase;
  }
  .card--back .rule {
    position: absolute;
    left: 150px; right: 150px;
    top: 206px;
    height: 1px;
    background: var(--teal);
  }
  .card--back .tagline {
    position: absolute;
    left: 0; right: 0;
    top: 226px;
    text-align: center;
    color: var(--card-white);
    font-size: 15px;
    letter-spacing: 0.4px;
  }

  /* Front side */
  .card--front {
    background: linear-gradient(160deg, var(--card-white) 55%, var(--paper-light) 100%);
  }
  .card--front .wordmark {
    position: absolute;
    left: 44px;
    top: 40px;
    color: var(--ink);
    font-size: 34px;
    font-weight: 700;
    letter-spacing: 1px;
    text-transform: uppercase;
  }
  .card--front .bands {
    position: absolute;
    inset: 0;
  }
  .contact {
    position: absolute;
    right: 40px;
    top: 176px;
    text-align: right;
    color: var(--ink);
  }
  .contact .name {
    color: var(--teal);
    font-size: 22px;
    font-weight: 700;
    margin-bottom: 4px;
  }
  .contact .role {
    font-size: 15px;
    line-height: 20px;
  }
  .contact .email {
    margin-top: 6px;
    font-size: 14px;
    color: var(--ink-soft);
  }
  .contact .email .label {
    color: var(--teal);
    font-weight: 700;
  }
  .website {
    position: absolute;
    right: 32px;
    bottom: 20px;
    color: var(--card-white);
    font-size: 14px;
    font-weight: 700;
    letter-spacing: 2px;
    white-space: nowrap;
  }
</style>
</head>
<body>
<main class="canvas">

  <section class="card card--back" aria-label="Business card, back">
    <div class="wordmark">Satchel &amp; Sundial</div>
    <div class="rule"></div>
    <p class="tagline">Live a life you don't need a holiday from</p>
  </section>

  <section class="card card--front" aria-label="Business card, front">
    <svg class="bands" width="640" height="366" viewBox="0 0 640 366" aria-hidden="true">
      <defs>
        <linearGradient id="teal-fade" x1="0" y1="0" x2="1" y2="0">
          <stop offset="0" stop-color="#25a796"/>
          <stop offset="1" stop-color="#3fbfae"/>
        </linearGradient>
        <linearGradient id="dark-fade" x1="0" y1="0" x2="1" y2="0">
          <stop offset="0" stop-color="#5a5a5c"/>
          <stop offset="0.1" stop-color="#2b2a2b"/>
          <stop offset="1" stop-color="#2b2a2b"/>
        </linearGradient>
      </defs>
      <polygon points="0,290 330,290 306,326 0,326" fill="url(#teal-fade)"/>
      <polygon points="318,306 640,306 640,366 270,366" fill="url(#dark-fade)"/>
    </svg>

    <div class="wordmark">Satchel &amp; Sundial</div>

    <div class="contact">
      <p class="name">Dorota Falkner</p>
      <p class="role">Your Lifestyle Business Coach</p>
      <p class="role">Retreat &amp; Trip Leader</p>
      <p class="email"><span class="label">E :</span> hello@satchelandsundial.example</p>
    </div>

    <p class="website">www.satchelandsundial.example</p>
  </section>

</main>
</body>
</html>
```